Website Redesign for MarrowArc.co.za – Bold, Modern & Professional Tattoo Supply Store (B2B ...

We’re looking for a skilled and creative web designer to redesign MarrowArc.co.za, a leading tattoo equipment and supplies store based in South Africa. The business serves both B2B (tattoo studios, artists, wholesalers) and B2C (individual customers) markets.

The current website is outdated and lacks the modern, edgy look that reflects the tattoo industry. We want a fresh, bold, and professional design that appeals to both professional artists and retail customers — combining trust, style, and functionality.

About the Business:
Marrow Arc supplies a wide range of tattoo-related products, including machines, needles, inks, hygiene supplies, and accessories. The company is well-established in the South African market and serves both individual tattoo artists and studios, as well as end customers looking for quality equipment.

The website must reflect the creative, bold, and artistic nature of the tattoo industry, while still being easy to navigate, fast, and conversion-focused.

What We’re Looking For:
A bold, modern design with a clear structure
Strong visual identity that reflects the tattoo culture — edgy, artistic, but still clean and professional
A layout that works for both B2B and B2C audiences
Clear product presentation and strong CTAs (Buy Now, Request Quote, Contact, etc.)
Fully responsive design (desktop + mobile)
Easy-to-navigate product categories and filters
Space for featured products, promotions, and artist-focused content
Integration of trust elements (payment icons, reviews, certifications, etc.)

Pages We Need Designed:
Homepage
Product detail page

Inspiration / Style Direction:
We’re looking for something with a strong personality, inspired by tattoo culture, but still clean and user-friendly. Think:

Dark theme with bold highlights (but open to light themes if well executed)
High-quality visuals and product imagery

Examples for inspiration:
GrimQuill.co.uk
Wexley RPN
Corvane Needle Supply
Brisk Tallow

Deliverables:
Full desktop and mobile designs (Figma, XD, or PSD)
All design source files
Fonts, icons, and assets used
Clearly labeled layers and organized files
Ready for development handoff

Target Market(s)

MarrowArc.co.za targets both B2B and B2C customers in South Africa: B2B: Professional tattoo artists, studios, and wholesalers looking for high-quality, reliable equipment and bulk pricing. B2C: Individual customers, hobbyists, and beginners seeking safe, affordable tattoo supplies with guidance and support. The site should appeal to both experienced professionals and newcomers, combining a bold, authentic tattoo vibe with a clean, user-friendly shopping experience.

Industry/Entity Type

Tattoo Equipment & Supplies – E-commerce (B2B & B2C)

Number of Pages Required

2 page

Requirements
Must have
• Responsive design, bold tattoo-inspired visual style, clear navigation for B2B & B2C, strong product presentation, clear call-to-actions, trust elements (reviews, badges, payment icons), category filters & search, dedicated B2B/wholesale info page, speed-optimized layout, easy access to contact & support.
Should not have
• Overly complex animations, cluttered layout, generic stock images, too many fonts or colors, hidden navigation, auto-play videos or sounds, outdated visual styles, low-quality product images, confusing checkout process, unnecessary pop-ups.

```html
<!DOCTYPE html>
<html lang="en">
<head>
<meta charset="utf-8">
<title>Marrow Arc – Tattoo Supplies</title>
<link href="https://fonts.googleapis.com/css2?family=Russo+One&family=Lato:ital,wght@0,400;0,700;1,400&display=swap" rel="stylesheet">
<style>
:root{
  --bg:#0b0b0b;
  --panel:#141414;
  --green:#3aa348;
  --white:#ffffff;
  --line:#2c2c2c;
  --star:#e0a526;
}
*{box-sizing:border-box;margin:0;padding:0}
html,body{width:1200px;height:5042px;overflow:hidden}
body{background:var(--bg);color:var(--white);font-family:"Lato",sans-serif;position:relative}
.abs{position:absolute}
.display{font-family:"Russo One",sans-serif;font-weight:400}
.hl{color:var(--green)}
.btn{position:absolute;display:flex;align-items:center;justify-content:center;background:var(--green);color:#fff;font-weight:700;font-size:16px;border-radius:5px;text-decoration:none}
.section-title{position:absolute;left:0;width:1200px;text-align:center;font-size:40px}

.header{position:absolute;left:0;top:0;width:1200px;height:110px;background:#0a0a0a}
.brand{position:absolute;left:112px;top:32px;font-weight:700;font-size:34px;letter-spacing:2px;color:#fff}
.search{position:absolute;left:434px;top:27px;width:511px;height:41px;border:2px solid #9a9a9a;border-radius:8px;background:#111;color:#aaa;font-size:14px;padding:10px 20px}
.nav{position:absolute;left:0;top:110px;width:1200px;height:55px;background:var(--green);display:flex;align-items:center;padding-left:114px;gap:29px;font-size:14px}

.hero{position:absolute;left:0;top:165px;width:1200px;height:579px;background:#070707}
.hero h1{position:absolute;left:108px;top:105px;font-size:60px;line-height:75px}
.hero .sub{position:absolute;left:108px;top:340px;font-size:21px}
.dots{position:absolute;display:flex;gap:8px}
.dots i{width:11px;height:11px;border-radius:50%;background:#fff;display:block}
.dots i.on{background:var(--green)}

.cat{position:absolute;width:310px;height:280px;background:var(--panel);border:1px solid #333}
.cat .ph{height:220px}
.cat p{text-align:center;font-size:21px;font-weight:700;margin-top:16px}

.about-img{position:absolute;left:0;top:1589px;width:597px;height:485px}
.about{position:absolute;left:597px;top:1589px;width:603px;height:485px;background:#0c0c0c}
.body-text{font-size:13px;line-height:30px;color:#e8e8e8}

.prod{position:absolute;width:231px}
.prod .ph{height:257px;border-radius:4px}
.prod .add{margin-top:20px;height:40px;background:var(--green);border-radius:5px;display:flex;align-items:center;justify-content:center;font-size:13px;font-weight:700}
.prod .name{margin-top:26px;font-size:19px;line-height:27px}
.stars{color:var(--star);font-size:19px;letter-spacing:1px}
.arrow{position:absolute;width:26px;height:26px;border-radius:50%;background:#fff}

.promo{position:absolute;left:112px;top:2810px;width:986px;height:458px;background:#141414;border-radius:8px;overflow:hidden}

.avatar{position:absolute;width:56px;height:56px;border-radius:50%;background:linear-gradient(#bfc6cc,#7b8790)}
.tname{position:absolute;font-size:17px;font-weight:700}
.tstars{position:absolute;font-size:12px;color:var(--star)}
.tquote{position:absolute;font-style:italic;font-size:13.5px;line-height:27px;color:#eee}

.artists{position:absolute;left:0;top:3820px;width:1200px;height:529px;background:#0e0e0e}

.badge{position:absolute;width:110px;height:110px;border-radius:50%;background:radial-gradient(circle,#e2c25a 0%,#b48a22 45%,#f1d67a 62%,#8c6a14 78%,#2a1f05 100%)}

.footer{position:absolute;left:0;top:4717px;width:1200px;height:325px;background:#0a0a0a}
.fcol{position:absolute;font-size:13px;line-height:29px;color:#ddd}
.fcol h4{color:var(--green);font-weight:400;font-size:15px;margin-bottom:6px}
.soc{width:24px;height:24px;border-radius:50%;background:#fff;display:inline-block;margin-right:6px}
.pay{display:inline-flex;align-items:center;justify-content:center;width:40px;height:22px;background:#2b3fa8;border-radius:3px;font-size:9px;font-weight:700;margin-left:5px}
</style>
</head>
<body>

<header class="header">
  <div class="brand">MARROW ARC</div>
  <div class="search">Search ...
    <svg class="abs" style="right:14px;top:10px" width="18" height="18" viewBox="0 0 18 18"><circle cx="7.5" cy="7.5" r="5.5" fill="none" stroke="#888" stroke-width="2"/><line x1="11.5" y1="11.5" x2="16" y2="16" stroke="#888" stroke-width="2"/></svg>
  </div>
  <svg class="abs" style="left:1033px;top:33px" width="50" height="22" viewBox="0 0 50 22">
    <circle cx="8" cy="6" r="5" fill="#fff"/><path d="M0 20 Q8 9 16 20Z" fill="#fff"/>
    <path d="M24 3h4l3 12h12l3-9H30" fill="none" stroke="#fff" stroke-width="2.5"/><circle cx="33" cy="19" r="2" fill="#fff"/><circle cx="42" cy="19" r="2" fill="#fff"/>
  </svg>
</header>
<nav class="nav">
  <span>Special Tattoo Ink</span><span>Medical Supplies</span><span>Needles</span><span>Furniture</span><span>Accessories</span><span>Consumables</span><span>Machines Piercing</span><span>Expired Products</span><span>Blog</span>
</nav>

<section class="hero">
  <div role="img" aria-label="Gloved hand holding a tattoo machine" class="abs" style="left:520px;top:0;width:680px;height:579px;background:radial-gradient(ellipse 55% 60% at 62% 45%,#4a1c1c 0%,#2a1111 35%,#140a0a 60%,#070707 100%)"></div>
  <h1 class="display">Premium <span class="hl">Tattoo</span><br><span class="hl">Equipment</span> for<br>Pros &amp; Creators</h1>
  <p class="sub">South Africa’s Leading Tattoo Supply Destination</p>
  <a class="btn" style="left:112px;top:389px;width:148px;height:51px">Request Quote</a>
  <div class="dots" style="left:574px;top:518px"><i></i><i class="on"></i><i></i></div>
</section>

<h2 class="section-title display" style="top:815px">Our <span class="hl">Categories</span></h2>
<div class="cat" style="left:115px;top:908px"><div class="ph" role="img" aria-label="Black and white tattoo ink bottles" style="background:linear-gradient(180deg,#2a2a2a 0%,#5a5a5a 45%,#c9c9c9 70%,#1a1a1a 100%)"></div><p>Tattoo Ink</p></div>
<div class="cat" style="left:446px;top:908px"><div class="ph" role="img" aria-label="Needle boxes with swirling night-sky print" style="background:linear-gradient(135deg,#15263f 0%,#2c4f8f 40%,#1b3566 65%,#0f1422 100%)"></div><p>Needles</p></div>
<div class="cat" style="left:777px;top:908px"><div class="ph" role="img" aria-label="Blue and pink macropin cartridges" style="background:linear-gradient(160deg,#2a2c33 0%,#4f8fa6 45%,#b56a95 60%,#1c1d22 100%)"></div><p>Macropin Cartridges</p></div>
<div class="cat" style="left:115px;top:1217px"><div class="ph" role="img" aria-label="Colourful printed machine grips" style="background:linear-gradient(135deg,#2f7d6a 0%,#b83a5c 35%,#d4a23a 65%,#1d1d1d 100%)"></div><p>Accessories</p></div>
<div class="cat" style="left:446px;top:1217px"><div class="ph" role="img" aria-label="Coil tattoo machine" style="background:radial-gradient(circle at 50% 45%,#5a5a5a 0%,#333 35%,#1a1a1a 70%)"></div><p>Tattoo Machines</p></div>
<div class="cat" style="left:777px;top:1217px"><div class="ph" role="img" aria-label="Coloured cohesive bandage rolls" style="background:linear-gradient(120deg,#d6336c 0%,#e37b2f 25%,#3d7fd1 50%,#48b85a 72%,#e8e8e8 90%)"></div><p>Consumables</p></div>

<div class="about-img" role="img" aria-label="Two tattoo artists working at a studio table, black and white" style="background:linear-gradient(120deg,#cfcfcf 0%,#8a8a8a 30%,#3a3a3a 55%,#bdbdbd 80%,#555 100%)"></div>
<section class="about">
  <h2 class="display abs" style="left:47px;top:65px;font-size:40px">About <span class="hl">Us</span></h2>
  <div class="abs body-text" style="left:45px;top:135px;width:430px">
    <p>MarrowArc is a professional tattoo equipment supplier based in Pretoria, South Africa. We provide high-quality machines, cartridges, traditional needles, inks, and studio essentials to artists and studios nationwide. Our focus is reliability, safety, and service.</p>
    <p style="margin-top:14px">We support professional artists and studios across South Africa with gear that meets strict performance and hygiene standards. Expect fast service, clear product info, and honest advice.</p>
  </div>
  <a class="btn" style="left:45px;top:384px;width:121px;height:49px">Read More</a>
</section>

<h2 class="section-title display" style="top:2155px">Featutred <span class="hl">Products</span></h2>
<div class="arrow" style="left:28px;top:2368px"><svg width="26" height="26" viewBox="0 0 26 26"><path d="M15 8l-5 5 5 5" fill="none" stroke="#000" stroke-width="2.5"/></svg></div>
<div class="arrow" style="left:1122px;top:2366px"><svg width="26" height="26" viewBox="0 0 26 26"><path d="M11 8l5 5-5 5" fill="none" stroke="#000" stroke-width="2.5"/></svg></div>
<div class="prod" style="left:115px;top:2250px"><div class="ph" role="img" aria-label="Black nitrile glove" style="background:radial-gradient(ellipse 35% 45% at 50% 50%,#151515 0%,#2a2a2a 55%,#f4f5f7 100%)"></div><div class="add">Add To Cart</div><p class="name">Black Nitrile Gloves</p><div class="stars">★★★★★</div></div>
<div class="prod" style="left:361px;top:2250px"><div class="ph" role="img" aria-label="Rolls of black sterile wrap tape" style="background:radial-gradient(ellipse 45% 35% at 50% 50%,#1e1e1e 0%,#3a3a3a 55%,#f4f5f7 100%)"></div><div class="add">Add To Cart</div><p class="name">SANIWRAP 100 MM X 100M</p><div class="stars">★★★★★</div></div>
<div class="prod" style="left:606px;top:2250px"><div class="ph" role="img" aria-label="Black tattoo ink bottle" style="background:radial-gradient(ellipse 22% 45% at 50% 55%,#111 0%,#2a2a2a 60%,#f4f5f7 100%)"></div><div class="add">Add To Cart</div><p class="name">Tattoo Ink</p><div class="stars">★★★★★</div></div>
<div class="prod" style="left:852px;top:2250px"><div class="ph" role="img" aria-label="Four blue liner cartridges" style="background:radial-gradient(ellipse 40% 40% at 50% 45%,#3fb6d9 0%,#9ad7ea 55%,#f4f5f7 100%)"></div><div class="add">Add To Cart</div><p class="name">QRN Tattoo Liner Cartridges -</p><div class="stars">★★★★★</div></div>

<section class="promo">
  <h2 class="display abs" style="left:35px;top:70px;font-size:40px;line-height:62px">Exclusive <span class="hl">Artist</span><br><span class="hl">Bundles</span> <span class="hl" style="font-family:Lato,sans-serif;font-size:50px">20%</span></h2>
  <p class="abs" style="left:39px;top:214px;width:380px;font-size:18px;line-height:37px;color:#eee">Upgrade your setup with high-performance rotary and coil machines trusted by top SA artists</p>
  <a class="btn" style="left:37px;top:351px;width:123px;height:49px">Buy Now</a>
  <div role="img" aria-label="Ink bottles, skull ornament and rotary machine bundle in a case" class="abs" style="left:481px;top:0;width:505px;height:458px;background:linear-gradient(135deg,#2a2a2e 0%,#d9d2bf 30%,#3a3a3a 50%,#6b3a8c 70%,#1e1e1e 100%)"></div>
</section>

<h2 class="section-title display" style="top:3428px">Client <span class="hl">Testimonials</span></h2>
<div class="avatar" style="left:106px;top:3545px" role="img" aria-label="Customer portrait"></div>
<p class="tname" style="left:184px;top:3555px">Lwazi Dube</p>
<p class="tstars" style="left:184px;top:3582px">★★★★★</p>
<p class="tquote" style="left:108px;top:3628px;width:410px">“Marrow Arc has completely upgraded the way we work in our studio. Their machines are powerful, consistent, and built for long sessions. The needle cartridges are some of the smoothest we’ve used, and deliveries are always fast and reliable.</p>
<div class="abs" style="left:597px;top:3535px;height:204px;border-left:2px dashed #444"></div>
<div class="avatar" style="left:672px;top:3545px" role="img" aria-label="Customer portrait"></div>
<p class="tname" style="left:753px;top:3555px">Pieter Nel</p>
<p class="tstars" style="left:753px;top:3582px">★★★★★</p>
<p class="tquote" style="left:674px;top:3628px;width:420px">“I ordered a tattoo machine and ink set from Marrow Arc and was blown away by the quality. Everything felt premium, and the machine runs smooth and quiet. Shipping was quick and the packaging was secure.</p>
<div class="dots" style="left:575px;top:3717px"><i></i><i class="on"></i><i></i></div>

<section class="artists">
  <h2 class="display abs" style="left:112px;top:80px;font-size:42px;line-height:60px"><span class="hl">Built for Artists</span><br>Who Demand More</h2>
  <div class="abs body-text" style="left:112px;top:228px;width:430px">
    <p>At Marrow Arc, we understand that every line, shade, and stroke is a reflection of your skill. That’s why we supply equipment engineered for precision, comfort, and consistency.</p>
    <p style="margin-top:14px">From powerful rotary machines to ultra-smooth needle cartridges, our products help you work with confidence — every session, every client.</p>
  </div>
  <a class="btn" style="left:113px;top:398px;width:108px;height:48px">Contact</a>
  <div role="img" aria-label="Two tattooed artists in black leather holding a branded parcel in a shop" class="abs" style="left:613px;top:0;width:587px;height:529px;background:linear-gradient(120deg,#3a2c2a 0%,#7a5a4a 30%,#1a1616 50%,#9a7860 70%,#231a18 100%)"></div>
</section>

<h2 class="section-title display" style="top:4432px">Our <span class="hl">Certification</span></h2>
<div class="badge" style="left:133px;top:4534px" role="img" aria-label="Certification seal"></div>
<div class="badge" style="left:293px;top:4534px" role="img" aria-label="Certification seal"></div>
<div class="badge" style="left:464px;top:4534px" role="img" aria-label="Certification seal"></div>
<div class="badge" style="left:632px;top:4534px" role="img" aria-label="Certification seal"></div>
<div class="badge" style="left:785px;top:4534px" role="img" aria-label="Certification seal"></div>
<div class="badge" style="left:951px;top:4534px" role="img" aria-label="Certification seal"></div>

<footer class="footer">
  <div class="abs" style="left:112px;top:80px;font-weight:700;font-size:32px;letter-spacing:2px">MARROW ARC</div>
  <div class="abs" style="left:112px;top:180px"><span class="soc"></span><span class="soc"></span><span class="soc"></span><span class="soc"></span></div>
  <div class="fcol" style="left:466px;top:80px"><h4>My Account</h4><p>Account</p><p>Order History</p><p>Wish List (0)</p><p>Newsletter</p></div>
  <div class="fcol" style="left:628px;top:80px"><h4>Other Links</h4><p>Privacy Policy</p><p>Terms &amp; Conditions</p><p>Disclaimer</p><p>Return Policy</p></div>
  <div class="fcol" style="left:826px;top:80px;line-height:22px"><h4>Contact Info</h4>
    <div style="position:relative;padding-left:44px"><span class="abs" style="left:0;top:4px;width:22px;height:22px;border-radius:50%;background:var(--green)"></span>Marrow Arc Pty Ltd<br>PO Box 4410 Silverton 0127</div>
    <div style="position:relative;padding-left:44px;margin-top:18px"><span class="abs" style="left:0;top:-8px;width:22px;height:22px;border-radius:50%;background:var(--green)"></span>0820000417</div>
    <div style="position:relative;padding-left:44px;margin-top:22px"><span class="abs" style="left:0;top:0;width:22px;height:22px;border-radius:50%;background:var(--green)"></span>info@marrowarc.co.za</div>
  </div>
  <div class="abs" style="left:112px;top:266px;width:976px;border-top:1px solid var(--line)"></div>
  <p class="abs" style="left:106px;top:288px;font-size:12px;letter-spacing:1px">Marrow Arc Pty Ltd © 2025</p>
  <div class="abs" style="left:820px;top:284px"><span class="pay">Kova</span><span class="pay">Lumo</span><span class="pay">Veyra</span><span class="pay">Paxa</span><span class="pay">Nuro</span><span class="pay">Arca</span></div>
</footer>

</body>
</html>
```